ecommerce news podcast artwork

Podcast cover art for a podcast featuring daily news and events around ecommerce product businesses.

text to be: BRISK LOOP
optional third line of text with smaller font: Podcast

looking for something that pops with a medium to light blue background. text can be in white/red/orange colors. prefer solid colors for text, but background can vary.
I'm really open to other ideas too, sometimes you don't know what you want until you see it.

Target Market(s)

ecommerce business owners, managers

Industry/Entity Type

news, business, ecommerce

Font styles to use
Sans Serif

Colors
0054AA
0677BA
7BADD7
CADEEF
E8F1F8
0094D4
00A9DD
6FCCEA
C7EBF8
E9F6FB
F0912C
F2A743
F7CA91
FBE8D2
FDF5EE
EB3D1F
EC4F4E
F09395
F8D3D4
FCEDEE

Requirements
Must have
• text: BRISK LOOP
Should not have
• no microphones, headsets/headphones, speakers, or other props like that.

```html
<!DOCTYPE html>
<html lang="en">
<head>
<meta charset="utf-8">
<title>Brisk Loop Podcast Cover</title>
<link rel="stylesheet" href="https://fonts.googleapis.com/css2?family=Montserrat:wght@300;800&display=swap">
<style>
  :root {
    --stage: #dddadb;
    --sky-deep: #9eeef6;
    --sky-mid: #b6f3f9;
    --sky-light: #dcfbfd;
    --ink: #242424;
    --orange: #ff7b00;
    --scene-lilac: #c9cdf0;
    --scene-coral: #ee6a55;
    --scene-gold: #f2c15e;
  }
  html, body {
    margin: 0;
    padding: 0;
    width: 1200px;
    height: 1121px;
    overflow: hidden;
    background: var(--stage);
  }
  .cover {
    position: absolute;
    left: 60px;
    top: 20px;
    width: 1080px;
    height: 1080px;
    overflow: hidden;
    background:
      radial-gradient(ellipse at 85% 40%, var(--sky-light) 0%, transparent 45%),
      radial-gradient(ellipse at 10% 60%, var(--sky-light) 0%, transparent 35%),
      linear-gradient(160deg, var(--sky-deep) 0%, var(--sky-mid) 50%, var(--sky-deep) 100%);
    font-family: "Montserrat", sans-serif;
  }
  .title {
    position: absolute;
    left: 106px;
    margin: 0;
    font-weight: 800;
    line-height: 1;
    white-space: nowrap;
  }
  .title-top {
    top: 256px;
    font-size: 240px;
    letter-spacing: -2px;
    color: var(--ink);
  }
  .title-bottom {
    top: 520px;
    font-size: 172px;
    letter-spacing: -2px;
    color: var(--orange);
  }
  .subtitle {
    position: absolute;
    left: 110px;
    top: 714px;
    margin: 0;
    font-weight: 300;
    font-size: 40px;
    line-height: 1;
    letter-spacing: 0.55em;
    color: var(--ink);
  }
  .shop-scene {
    position: absolute;
    left: 650px;
    top: 512px;
    width: 430px;
    height: 405px;
    border-radius: 40px 0 0 40px;
    background:
      radial-gradient(ellipse at 45% 45%, #ffffff 0%, rgba(255,255,255,0.6) 30%, transparent 60%),
      linear-gradient(135deg, var(--scene-lilac) 0%, var(--scene-coral) 60%, var(--scene-gold) 100%);
    opacity: 0.85;
  }
</style>
</head>
<body>
  <main class="cover">
    <h1 class="title title-top">BRISK</h1>
    <p class="title title-bottom">LOOP</p>
    <p class="subtitle">PODCAST</p>
    <div class="shop-scene" role="img" aria-label="Illustration of a smartphone showing a clothing store, with shopping bags, a coin, a discount badge, a buy button and a shopping cart"></div>
  </main>
</body>
</html>
```